Medical consulting firm needs polished website

I am a physician and working on setting up a smal consulting firm in New Hampshire, USA. It is called Bright Harbor Medical Services, LLC and the website will be BrightHarborMed.com. I was puttering around at making my own website, and it just didn't come together nicely so I've decided to leave it to the pros. The focus of the business is Advanced Care Planning, ie planning for your future medical needs. So it deals with some heavy stuff like planning for if you get sick, who should make decisions for you, end of life options etc. So it can't be too flippant or cutesy, but also can't be too dour and dark. I am hoping to convey that by thinking ahead and making some plans you can lift some of the worries off of yourself and your family - and that we can help make a scary sounding path more manageable. I want it to be made with wordpress and I have actually already bought a template ( Vitarun – A Modern Multidisciplinary Medical & Health Theme ). The website needs to have general information about our services, doc profile, appointment maker, blog/url link page, and ideally web commerce application ( the template has access to woocommerce). I've posted my business card and current brochure (still tweaking them, but you get the idea). I am also partnering with lumenfold.com and so have included their logo and would want connections/info about them. I have the logos etc in different formats as needed.

Target Market(s)

middle aged to older adults

Industry/Entity Type

Medical

Coding

Coded - Design and coding required

Font styles to use
Sans Serif

Requirements
Must have
• as above.
Nice to have
• Ease of reading/access for elderly viewers. woo commerce.

```html
<!DOCTYPE html>
<html lang="en">
<head>
<meta charset="utf-8">
<title>Bright Harbor Medical Services</title>
<link rel="stylesheet" href="https://fonts.googleapis.com/css2?family=Open+Sans:ital,wght@0,400;0,600;0,700;1,400&family=Montserrat:wght@400;700;800&display=swap">
<style>
:root{
  --green:#3aa84a;
  --green-dark:#2f9140;
  --blue:#2f77bf;
  --blue-light:#4e92d3;
  --ink:#222;
  --text:#555;
  --muted:#888;
  --line:#e2e2e2;
  --footer:#f4f4f4;
  --white:#fff;
}
*{margin:0;padding:0;box-sizing:border-box}
html,body{width:1200px;height:2826px;overflow:hidden}
body{position:relative;font-family:"Open Sans",Arial,sans-serif;color:var(--text);background:var(--white)}
.abs{position:absolute}

/* header */
.brand{left:98px;top:16px;height:62px;display:flex;align-items:center;gap:10px}
.brand-mark{width:62px;height:62px;border-radius:50%;background:var(--blue)}
.brand-name{font-size:30px;font-weight:600;color:var(--blue);line-height:1}
.contact-chip{display:flex;align-items:center;gap:12px;top:28px}
.contact-chip .ico{width:26px;height:26px;border-radius:50%;border:2px solid var(--green);display:flex;align-items:center;justify-content:center}
.contact-chip small{display:block;font-size:11px;font-weight:600;color:var(--ink);letter-spacing:.3px}
.contact-chip b{display:block;font-size:17px;font-weight:600;color:var(--ink)}
.social{top:32px;left:948px;display:flex;gap:10px}
.social span{width:32px;height:32px;border-radius:50%}

/* nav */
.nav{top:96px;left:0;width:1200px;height:40px;border-top:1px solid var(--line)}
.nav a{position:absolute;top:9px;font-size:15px;font-weight:600;color:var(--ink);text-decoration:none}
.nav a.active{color:var(--green)}
.plan-btn{left:868px;top:96px;width:232px;height:40px;background:var(--green);color:var(--white);font-size:16px;font-weight:700;display:flex;align-items:center;justify-content:center}

/* hero */
.hero{top:136px;left:0;width:1200px;height:476px;overflow:hidden}
.hero-photo{position:absolute;inset:0;background:linear-gradient(100deg,#f6f2c6 0%,#eae38a 35%,#c9c888 60%,#a8a27a 100%)}
.hero-kicker{left:98px;top:254px;font-size:28px;color:var(--ink)}
.hero-title{left:96px;top:292px;font-family:"Montserrat",sans-serif;font-size:44px;font-weight:800;color:#1b1b1b;letter-spacing:.5px}
.btn-outline{display:flex;align-items:center;justify-content:center;border:2px solid #555;font-size:14px;font-weight:700;color:var(--ink)}
.hero-dots{left:568px;top:550px;display:flex;gap:6px}
.hero-dots i{width:11px;height:11px;border-radius:50%;border:1px solid var(--white)}
.hero-dots i.on{background:var(--white)}

/* welcome */
.welcome-photo{left:98px;top:663px;width:460px;height:283px;background:linear-gradient(135deg,#dfe3e8,#aab3bd 60%,#7d8792)}
.play{left:305px;top:777px}
.h2{font-size:28px;font-weight:400;color:var(--ink)}
.copy{font-size:13px;line-height:23px;color:var(--muted)}
.more{font-size:12.5px;font-weight:700;color:var(--green);letter-spacing:.3px}

/* testimonial */
.quote-band{top:995px;left:0;width:1200px;height:333px;background:linear-gradient(120deg,var(--blue-light),var(--blue) 55%,#2a6cae)}
.avatar{left:550px;top:1033px;width:100px;height:100px;border-radius:50%;border:4px solid var(--white);background:#c79e88}
.quote-text{left:300px;top:1160px;width:600px;text-align:center;font-size:14px;font-style:italic;line-height:27px;color:var(--white)}
.quote-mark{left:278px;top:1136px;font-size:30px;color:var(--white);font-family:Georgia,serif}
.quote-name{left:0;width:1200px;top:1262px;text-align:center;font-size:18px;font-weight:600;color:var(--white)}

/* services */
.services-art{left:528px;top:1328px;width:672px;height:509px;background:radial-gradient(circle at 60% 45%,#f5fbff 0%,#cfe7f5 45%,#8ec1dd 100%)}
.services-fade{left:0;top:1328px;width:760px;height:509px;background:linear-gradient(90deg,#fff 62%,rgba(255,255,255,0))}
.service{left:100px;display:flex;align-items:center;gap:34px;font-size:14.5px;font-weight:600;color:#333}
.service svg{width:56px;height:56px}

/* blog */
.blog-title{left:0;width:1200px;top:1880px;text-align:center;font-size:28px;font-weight:400;color:var(--ink)}
.card{top:1944px;width:322px}
.card-photo{width:322px;height:217px;position:relative}
.card-date{position:absolute;right:0;bottom:0;background:rgba(40,40,40,.85);color:var(--white);font-size:16px;font-weight:600;padding:6px 10px;display:flex;gap:8px;align-items:center}
.card h3{font-size:18px;font-weight:600;color:var(--ink);margin:14px 0 6px}
.card p{font-size:11.5px;line-height:19px;color:var(--muted)}
.card .more{display:block;margin-top:12px}
.view-more{left:512px;top:2338px;width:174px;height:43px;border:2px solid #bbb;font-size:13px;font-weight:700;color:var(--green);display:flex;align-items:center;justify-content:center}

/* footer */
.footer{left:0;top:2430px;width:1200px;height:396px;background:var(--footer)}
.partner{left:98px;top:2548px;display:flex;align-items:center;gap:10px}
.partner .dot{width:40px;height:40px;border-radius:50%;background:#2b5a8a}
.partner b{font-size:44px;font-weight:400;color:#2b5a8a;letter-spacing:-.5px}
.f-head{top:2487px;font-size:18px;font-weight:600;color:var(--ink)}
.f-links{left:433px;top:2527px;font-size:12px;line-height:26.5px;color:var(--text);list-style:none}
.f-contact{left:588px;top:2527px;font-size:12px;color:var(--text)}
.f-contact div{display:flex;gap:12px;line-height:19px;margin-bottom:26px}
.map{left:825px;top:2534px;width:277px;height:156px;border:1px solid #ccc;background:linear-gradient(135deg,#eef0ea,#dfe3da)}
.f-rule{left:98px;top:2717px;width:1004px;height:1px;background:#ddd}
.news-label{left:98px;top:2740px;font-size:15px;font-weight:600;color:var(--ink)}
.news-input{left:98px;top:2769px;width:334px;height:35px;border:1px solid #ccc;background:var(--white)}
.news-btn{left:432px;top:2769px;width:80px;height:35px;background:var(--green);color:var(--white);font-size:12.5px;font-weight:700;display:flex;align-items:center;justify-content:center}
.f-social{left:898px;top:2746px;display:flex;gap:9px}
.f-social span{width:34px;height:34px;border-radius:50%;border:1.5px solid #aaa}
.copyright{left:720px;top:2792px;width:382px;text-align:right;font-size:11px;color:var(--muted)}
</style>
</head>
<body>

<!-- header -->
<div class="abs brand">
  <span class="brand-mark"></span>
  <div class="brand-name">Bright Harbor</div>
</div>
<div class="abs contact-chip" style="left:460px">
  <span class="ico"><svg width="12" height="12" viewBox="0 0 24 24"><path fill="#3aa84a" d="M6.6 10.8a15.2 15.2 0 0 0 6.6 6.6l2.2-2.2c.3-.3.7-.4 1-.2 1.1.4 2.3.6 3.6.6.6 0 1 .4 1 1V20c0 .6-.4 1-1 1A17 17 0 0 1 3 4c0-.6.4-1 1-1h3.5c.6 0 1 .4 1 1 0 1.3.2 2.5.6 3.6.1.3 0 .7-.2 1z"/></svg></span>
  <div><small>CALL US ON :</small><b>603-555-0142</b></div>
</div>
<div class="abs contact-chip" style="left:648px">
  <span class="ico"><svg width="12" height="12" viewBox="0 0 24 24"><path fill="#3aa84a" d="M2 5h20v14H2zm2 2v.5l8 5 8-5V7z"/></svg></span>
  <div><small>EMAIL US ON :</small><b>info@brightharbormed.com</b></div>
</div>
<div class="abs social">
  <span style="background:#3b5998"></span><span style="background:#2fa8e0"></span><span style="background:#dd4b39"></span><span style="background:#1f6fa3"></span>
</div>

<!-- nav -->
<nav class="abs nav">
  <a class="active" style="left:100px">Home</a>
  <a style="left:192px">About Us</a>
  <a style="left:311px">Services</a>
  <a style="left:418px">Planning</a>
  <a style="left:535px">Blog</a>
  <a style="left:616px">Contact Us</a>
  <a style="left:746px;top:8px"><svg width="18" height="18" viewBox="0 0 24 24"><circle cx="10" cy="10" r="6.5" fill="none" stroke="#222" stroke-width="3"/><path d="M15 15l6 6" stroke="#222" stroke-width="3"/></svg></a>
</nav>
<div class="abs plan-btn">MAKE MY PLAN</div>

<!-- hero -->
<section class="abs hero">
  <div class="hero-photo" role="img" aria-label="Smiling older couple outdoors in warm sunlight"></div>
  <svg class="abs" style="left:0;bottom:0" width="1200" height="90" viewBox="0 0 1200 90">
    <path d="M0 40 Q600 110 1200 20 L1200 90 L0 90Z" fill="#3aa84a"/>
    <path d="M0 62 Q600 125 1200 48 L1200 90 L0 90Z" fill="#fff"/>
  </svg>
</section>
<div class="abs hero-kicker">Bright Harbor Medical Services</div>
<div class="abs hero-title">BECAUSE SOMEDAY IS SOON</div>
<div class="abs btn-outline" style="left:98px;top:362px;width:134px;height:40px">READ MORE &gt;&gt;</div>
<div class="abs hero-dots"><i class="on"></i><i></i><i></i><i></i></div>

<!-- welcome -->
<div class="abs welcome-photo" role="img" aria-label="Stethoscope resting on a medical benefits statement"></div>
<svg class="abs play" width="46" height="46" viewBox="0 0 46 46"><circle cx="23" cy="23" r="20" fill="rgba(255,255,255,.35)" stroke="#fff" stroke-width="3"/><path d="M18 14l13 9-13 9z" fill="#fff"/></svg>
<h2 class="abs h2" style="left:599px;top:662px">Welcome to Bright Harbor Medical Services</h2>
<p class="abs copy" style="left:599px;top:713px;width:500px">At vero eos et accusamus et iusto odio dignissimos ducimus qui blanditiis praesentium voluptatum deleniti atque corrupti quos.</p>
<p class="abs copy" style="left:599px;top:784px;width:500px">Dolores et quas molestias excepturi sint occaecati cupiditate non provident, similiqusu nt in culpa qui officia deserunt mollitia animi, id est laborum et dolorum fuga. Et hrum quidem rerum facilis est et expedita distinctio. Nam libero tempore, cum soluta nobest eligendi optio cumque nihil impedit quo minus id quod maxime placeat facere pomus, omnis voluptas assumenda est, omnis dolor repell.</p>
<div class="abs more" style="left:599px;top:924px">READ MORE &#8594;</div>

<!-- testimonial -->
<section class="abs quote-band"></section>
<div class="abs avatar" role="img" aria-label="Portrait of a client"></div>
<div class="abs quote-mark">&#8220;</div>
<p class="abs quote-text">At vero eos et accusamus et iusto odio dignissimos ducimus qblan ditiis praesentium voluptatum deleniti atque corrupti quos dolores et quas molestias excepturi sint occae cati cupiditate non providentsimili que sunt in culpa q quidem rerum</p>
<div class="abs quote-name">- Mark Ellison</div>

<!-- services -->
<div class="abs services-art" role="img" aria-label="Hand touching a glowing network of medical icons around a central emblem"></div>
<div class="abs services-fade"></div>
<h2 class="abs h2" style="left:103px;top:1376px">Our Services Include</h2>
<div class="abs service" style="top:1441px">
  <svg viewBox="0 0 56 56" fill="none" stroke="#3aa84a" stroke-width="2.2"><path d="M28 12a11 11 0 0 0-7 19.5c1.5 1.3 2 3 2 4.5h10c0-1.5.5-3.2 2-4.5A11 11 0 0 0 28 12z"/><path d="M23 40h10M24 44h8M28 4v4M12 20h-4M48 20h-4M16 9l3 3M40 9l-3 3"/></svg>
  Individualized physician-guided healthcare planning</div>
<div class="abs service" style="top:1517px">
  <svg viewBox="0 0 56 56" fill="none" stroke="#3aa84a" stroke-width="2.2"><path d="M8 38l12-12 8 4 8-8 12 8"/><path d="M14 44l14-14M34 44L20 30"/><path d="M4 34l6 8M52 30l-6 8"/></svg>
  Helping navigate complex medical situations</div>
<div class="abs service" style="top:1592px">
  <svg viewBox="0 0 56 56" fill="none" stroke="#3aa84a" stroke-width="2.2"><circle cx="28" cy="28" r="9"/><path d="M28 6v7M28 43v7M6 28h7M43 28h7M12 12l5 5M39 39l5 5M44 12l-5 5M17 39l-5 5"/></svg>
  Creating legally binding Advanced Directives</div>
<div class="abs service" style="top:1668px">
  <svg viewBox="0 0 56 56" fill="none" stroke="#3aa84a" stroke-width="2.2"><rect x="8" y="24" width="20" height="10" rx="5" transform="rotate(-45 18 29)"/><rect x="28" y="22" width="20" height="10" rx="5" transform="rotate(-45 38 27)"/><path d="M23 33l10-10"/></svg>
  Sharing your decisions with your loved ones and your doctor</div>
<div class="abs service" style="top:1741px">
  <svg viewBox="0 0 56 56" fill="none" stroke="#3aa84a" stroke-width="2.2"><path d="M28 6l18 6v14c0 12-8 20-18 24C18 46 10 38 10 26V12z"/><path d="M20 28l6 6 11-12"/></svg>
  Secure, accessible, web-based storage of your documents</div>

<!-- blog -->
<h2 class="abs blog-title">Latest Blog</h2>
<article class="abs card" style="left:98px">
  <div class="card-photo" role="img" aria-label="Doctor comforting an older patient" style="background:linear-gradient(135deg,#d9e4ef,#9fb4c9)"><span class="card-date">&#9635; 12/05/2016</span></div>
  <h3>Finibus Bonorum et Malorum</h3>
  <p>Nam libero tempore, cum soluta nobis est eligendi optio cumque nihil impedit quo minus id quod maxime placeat facere possimu ssumenda est.</p>
  <span class="more">READ MORE &gt;&gt;</span>
</article>
<article class="abs card" style="left:439px">
  <div class="card-photo" role="img" aria-label="Lab scientist examining a test tube" style="background:linear-gradient(135deg,#e8ecef,#b5c3cf)"><span class="card-date">&#9635; 12/05/2016</span></div>
  <h3>Finibus Bonorum et Malorum</h3>
  <p>Nam libero tempore, cum soluta nobis est eligendi optio cumque nihil impedit quo minus id quod maxime placeat facere possimu ssumenda est.</p>
  <span class="more">READ MORE &gt;&gt;</span>
</article>
<article class="abs card" style="left:780px">
  <div class="card-photo" role="img" aria-label="Doctor examining a young child with a stethoscope" style="background:linear-gradient(135deg,#eef1f3,#aec0d2)"><span class="card-date">&#9635; 12/05/2016</span></div>
  <h3>Finibus Bonorum et Malorum</h3>
  <p>Nam libero tempore, cum soluta nobis est eligendi optio cumque nihil impedit quo minus id quod maxime placeat facere possimu ssumenda est.</p>
  <span class="more">READ MORE &gt;&gt;</span>
</article>
<div class="abs view-more">VIEW MORE BLOG</div>

<!-- footer -->
<footer class="abs footer"></footer>
<svg class="abs" style="left:0;top:2420px" width="1200" height="30" viewBox="0 0 1200 30"><path d="M0 10 Q600 -6 1200 10" fill="none" stroke="#e4e4e4" stroke-width="3"/></svg>
<div class="abs partner"><span class="dot"></span><b>lumenfold</b></div>
<h4 class="abs f-head" style="left:433px">Information</h4>
<h4 class="abs f-head" style="left:588px">Contact Address</h4>
<h4 class="abs f-head" style="left:825px">Location</h4>
<ul class="abs f-links"><li>Home</li><li>About Us</li><li>Services</li><li>Planning</li><li>Blog</li><li>Contact Us</li></ul>
<div class="abs f-contact">
  <div><svg width="12" height="16" viewBox="0 0 12 16"><path d="M6 0a6 6 0 0 0-6 6c0 4.5 6 10 6 10s6-5.5 6-10a6 6 0 0 0-6-6zm0 8.5A2.5 2.5 0 1 1 6 3.5a2.5 2.5 0 0 1 0 5z" fill="#3aa84a"/></svg><span>14 Maple Ridge Road, Concord,<br>New Hampshire, USA</span></div>
  <div><svg width="14" height="14" viewBox="0 0 24 24"><path fill="#3aa84a" d="M6.6 10.8a15.2 15.2 0 0 0 6.6 6.6l2.2-2.2c.3-.3.7-.4 1-.2 1.1.4 2.3.6 3.6.6.6 0 1 .4 1 1V20c0 .6-.4 1-1 1A17 17 0 0 1 3 4c0-.6.4-1 1-1h3.5c.6 0 1 .4 1 1 0 1.3.2 2.5.6 3.6.1.3 0 .7-.2 1z"/></svg><span>603-555-0142</span></div>
  <div><svg width="14" height="14" viewBox="0 0 24 24"><path fill="#3aa84a" d="M5 3h10v6h4v12H5zm2 8v2h10v-2zm0 4v2h10v-2z"/></svg><span>603-555-0187</span></div>
  <div><svg width="14" height="14" viewBox="0 0 24 24"><path fill="#3aa84a" d="M2 5h20v14H2zm2 2v.5l8 5 8-5V7z"/></svg><span>info@brightharbormed.com</span></div>
</div>
<div class="abs map" role="img" aria-label="Street map marking the office location"></div>
<div class="abs f-rule"></div>
<div class="abs news-label">Newsletter Sign-up</div>
<div class="abs news-input"></div>
<div class="abs news-btn">SIGN UP</div>
<div class="abs f-social"><span></span><span></span><span></span><span></span><span></span></div>
<div class="abs copyright">Copyrights © 2016, Bright Harbor Medical Services. All Rights Reserved.</div>

</body>
</html>
```